Open sky harmony Business cards - yoga studio

We need business cards for our yoga studio Opensky Harmony.
We would like to see designs that include the colour blue and our logo.
The business card should communicate a feeling of strength and calm

Requirements
Must have
• The business card must include
"Mirela Thornquist - Director"
and
"42 Wattlecrest Avenue
Dunmoreton
VIC 3917
Ph - 0471 586 204"

```html
<!DOCTYPE html>
<html lang="en">
<head>
<meta charset="utf-8">
<title>Opensky Harmony – Business Cards</title>
<link href="https://fonts.googleapis.com/css2?family=Arimo:wght@400;700&display=swap" rel="stylesheet">
<style>
  :root {
    --brand-blue: #6db5cc;
    --mist-blue: #dde9f0;
    --card-white: #ffffff;
    --page-bg: #ffffff;
    --card-shadow: rgba(0, 0, 0, 0.28);
  }
  * { margin: 0; padding: 0; box-sizing: border-box; }
  html, body {
    width: 1200px;
    height: 1000px;
    overflow: hidden;
    background: var(--page-bg);
    font-family: "Arimo", Arial, sans-serif;
  }
  .card {
    position: absolute;
    left: 226px;
    width: 745px;
    height: 459px;
    box-shadow: 3px 4px 8px var(--card-shadow);
    overflow: hidden;
  }
  .card--front {
    top: 20px;
    background: var(--brand-blue);
    color: var(--card-white);
    display: flex;
    flex-direction: column;
    align-items: center;
    justify-content: center;
  }
  .brand-dot {
    width: 70px;
    height: 70px;
    border-radius: 50%;
    background: var(--card-white);
    margin-bottom: 34px;
  }
  .brand-name {
    font-size: 54px;
    font-weight: 400;
    letter-spacing: 1px;
    line-height: 1;
  }
  .brand-services {
    margin-top: 20px;
    font-size: 15px;
    letter-spacing: 1px;
  }
  .card--back {
    top: 511px;
    background: var(--card-white);
  }
  .side-panel {
    position: absolute;
    left: 0;
    top: 0;
    width: 372px;
    height: 100%;
    background: var(--mist-blue);
  }
  .side-panel__dot {
    position: absolute;
    left: 46px;
    top: 140px;
    width: 280px;
    height: 280px;
    border-radius: 50%;
    background: var(--brand-blue);
  }
  .contact {
    position: absolute;
    left: 400px;
    top: 182px;
    color: var(--brand-blue);
  }
  .contact__name {
    font-size: 33px;
    font-weight: 700;
    line-height: 1;
  }
  .contact__role {
    margin-top: 12px;
    font-size: 23px;
    line-height: 1;
  }
  .contact__list {
    list-style: none;
    margin-top: 52px;
    font-size: 24px;
    line-height: 30px;
  }
  .contact__item {
    display: flex;
    align-items: flex-start;
    margin-bottom: 10px;
  }
  .contact__icon {
    width: 22px;
    height: 22px;
    margin: 4px 16px 0 0;
    flex: none;
  }
</style>
</head>
<body>

<section class="card card--front" aria-label="Business card front">
  <div class="brand-dot"></div>
  <h1 class="brand-name">Opensky Harmony</h1>
  <p class="brand-services">YOGA · FITNESS · AQUA</p>
</section>

<section class="card card--back" aria-label="Business card back">
  <div class="side-panel" role="img" aria-label="Soft blue side panel with brand circle">
    <div class="side-panel__dot"></div>
  </div>

  <div class="contact">
    <h2 class="contact__name">Mirela Thornquist</h2>
    <p class="contact__role">DIRECTOR</p>
    <ul class="contact__list">
      <li class="contact__item">
        <svg class="contact__icon" viewBox="0 0 24 24" aria-hidden="true">
          <path d="M12 2C8 2 5 5 5 9c0 5 7 13 7 13s7-8 7-13c0-4-3-7-7-7zm0 10a3 3 0 1 1 0-6 3 3 0 0 1 0 6z" fill="var(--brand-blue)"/>
        </svg>
        <span>42 Wattlecrest Avenue,<br>Dunmoreton VIC 3917</span>
      </li>
      <li class="contact__item">
        <svg class="contact__icon" viewBox="0 0 24 24" aria-hidden="true">
          <path d="M6.6 10.8a15 15 0 0 0 6.6 6.6l2.2-2.2a1 1 0 0 1 1-.25 11.4 11.4 0 0 0 3.6.57 1 1 0 0 1 1 1V20a1 1 0 0 1-1 1A17 17 0 0 1 3 4a1 1 0 0 1 1-1h3.5a1 1 0 0 1 1 1c0 1.250.2 2.45.57 3.57a1 1 0 0 1-.25 1z" fill="var(--brand-blue)"/>
        </svg>
        <span>0471 586 204</span>
      </li>
    </ul>
  </div>
</section>

</body>
</html>
```